Redesign business cards

We have a new logo and I am not that happy with the layout of our existing card and looking for a change. Font is a bit small and the green can be hard to read. Logo may need a tidy up as the copy I have is not that hi-res too so require you to produce a hi-res version of the logo for us too. There will be three individual business cards to produce with just the names and phone numbers being different. Address will change too, but use what you see on the card for now.

Industry/Entity Type

Business

Requirements
Nice to have
• You could consider a redesign to the new logo, just not too radical. We like the blue and green hexagons as we feel that they are representative of oil industry that we are in.

```html
<!DOCTYPE html>
<html lang="en">
<head>
<meta charset="utf-8">
<title>NovaLube Oil Services – Business Card</title>
<link rel="stylesheet" href="https://fonts.googleapis.com/css2?family=Arimo:wght@400;700&display=swap">
<style>
  :root {
    --backdrop: #3f4e59;
    --card: #ffffff;
    --brand-blue: #1ba8e0;
    --brand-green: #86bc3a;
    --ink: #111111;
    --icon-grey: #8a8f94;
    --on-band: #ffffff;
  }
  * { box-sizing: border-box; margin: 0; padding: 0; }
  html, body {
    width: 1200px;
    height: 1000px;
    overflow: hidden;
    background: var(--backdrop);
    font-family: "Arimo", Arial, sans-serif;
  }
  .business-card {
    position: absolute;
    left: 100px;
    top: 215px;
    width: 1000px;
    height: 570px;
    background: var(--card);
    overflow: hidden;
    box-shadow: 0 10px 30px rgba(0,0,0,0.35);
  }
  .wave-band {
    position: absolute;
    inset: 0;
    width: 100%;
    height: 100%;
  }
  .wordmark {
    position: absolute;
    left: 70px;
    top: 200px;
    display: flex;
    align-items: center;
    gap: 16px;
  }
  .wordmark-square {
    width: 34px;
    height: 34px;
    background: var(--brand-blue);
  }
  .wordmark-name {
    color: var(--brand-blue);
    font-weight: 700;
    font-size: 44px;
    line-height: 1.05;
    width: 260px;
  }
  .holder {
    position: absolute;
    right: 60px;
    top: 100px;
    text-align: right;
  }
  .holder-name {
    color: var(--brand-blue);
    font-size: 31px;
    font-weight: 400;
  }
  .holder-role {
    color: var(--brand-green);
    font-size: 25px;
    margin-top: 6px;
  }
  .contact-list {
    position: absolute;
    left: 620px;
    top: 196px;
    list-style: none;
  }
  .contact-item {
    display: flex;
    align-items: center;
    gap: 14px;
    color: var(--ink);
    font-size: 25px;
    line-height: 36px;
  }
  .contact-icon { width: 20px; height: 20px; flex: none; }
  .address {
    position: absolute;
    left: 34px;
    bottom: 32px;
    display: flex;
    align-items: center;
    gap: 12px;
    color: var(--on-band);
    font-size: 21px;
  }
  .address-pin { width: 18px; height: 24px; }
</style>
</head>
<body>
  <article class="business-card">
    <svg class="wave-band" viewBox="0 0 1000 570" preserveAspectRatio="none" aria-hidden="true">
      <path fill="var(--brand-green)" d="M0,445 C260,436 480,388 700,370 C860,358 950,356 1000,342 V570 H0 Z"/>
      <path fill="var(--brand-blue)" d="M0,472 C270,464 500,408 720,390 C870,378 950,374 1000,362 V570 H0 Z"/>
    </svg>

    <div class="wordmark">
      <span class="wordmark-square"></span>
      <span class="wordmark-name">NovaLube Oil Services</span>
    </div>

    <header class="holder">
      <h1 class="holder-name">Daniel Hartley NZCE (Mech) P&amp;P</h1>
      <p class="holder-role">Director</p>
    </header>

    <ul class="contact-list">
      <li class="contact-item">
        <svg class="contact-icon" viewBox="0 0 24 24" aria-hidden="true"><path fill="var(--icon-grey)" d="M6.6 10.8a15 15 0 0 0 6.6 6.6l2.2-2.2a1 1 0 0 1 1-.25 11.4 11.4 0 0 0 3.6.57 1 1 0 0 1 1 1V20a1 1 0 0 1-1 1A17 17 0 0 1 3 4a1 1 0 0 1 1-1h3.5a1 1 0 0 1 1 1c0 1.25.2 2.45.57 3.57a1 1 0 0 1-.25 1z"/></svg>
        <span>+614 555 01234</span>
      </li>
      <li class="contact-item">
        <svg class="contact-icon" viewBox="0 0 24 24" aria-hidden="true"><rect x="2" y="5" width="20" height="14" fill="var(--icon-grey)"/><path d="M2 5l10 8 10-8" fill="none" stroke="#fff" stroke-width="1.6"/></svg>
        <span>daniel@novaclean.co.nz</span>
      </li>
      <li class="contact-item">
        <svg class="contact-icon" viewBox="0 0 24 24" aria-hidden="true"><g fill="none" stroke="var(--icon-grey)" stroke-width="1.6"><circle cx="12" cy="12" r="9"/><ellipse cx="12" cy="12" rx="4" ry="9"/><path d="M3 12h18M5 7h14M5 17h14"/></g></svg>
        <span>www.novalube.com.au</span>
      </li>
    </ul>

    <p class="address">
      <svg class="address-pin" viewBox="0 0 18 24" aria-hidden="true"><path fill="#fff" d="M9 0a9 9 0 0 0-9 9c0 6.5 9 15 9 15s9-8.5 9-15a9 9 0 0 0-9-9zm0 12.5A3.5 3.5 0 1 1 9 5.5a3.5 3.5 0 0 1 0 7z"/></svg>
      <span>NovaLube Oil Services 512 Harbour Road / PO Box 4410 / Eastvale Queensland 4000</span>
    </p>
  </article>
</body>
</html>
```